KDWB Business Card

Looking for a business card design to incorporate our branding. We want to only use the colors listing in the Branding Package (attached).
Updates

Target Market(s)

People who need their phone or device fixed.

Industry/Entity Type

Electronics

Contact Information for Business Card

Please use:

Brightwick Gadget Clinic LLC
4810 E Harlow Ridge Rd
Suite 417
San Antonio, TX 78163

Marcus Delgrove, Store Manager

(210) 555-0147

Requirements
Must have
• Must include the colors that are contained within the Branding Package PDF file.

```html
<!DOCTYPE html>
<html lang="en">
<head>
<meta charset="utf-8">
<title>Brightwick Gadget Clinic – Business Card</title>
<link rel="stylesheet" href="https://fonts.googleapis.com/css2?family=Arimo:wght@400;500&display=swap">
<style>
  :root {
    --backdrop: #3a3532;
    --orange: #f05a1e;
    --frame-grey: #4b4c4e;
    --paper: #ececec;
    --ink: #2a2a2a;
    --rule: #9a9a9a;
    --card-black: #1d1d1d;
  }
  * { box-sizing: border-box; margin: 0; padding: 0; }
  html, body { width: 1200px; height: 764px; overflow: hidden; }
  body {
    background: var(--backdrop);
    font-family: "Arimo", Arial, sans-serif;
    position: relative;
  }
  .card {
    position: absolute;
    top: 239px;
    width: 500px;
    height: 286px;
    box-shadow: 0 10px 24px rgba(0,0,0,0.45);
  }
  .card-front { left: 60px; background: var(--frame-grey); padding: 16px; }
  .card-back  { left: 640px; background: var(--card-black); display: flex; align-items: center; justify-content: center; }

  .front-panel {
    width: 100%; height: 100%;
    background: var(--paper);
    display: flex;
    align-items: center;
  }
  .brand-area {
    width: 48%;
    height: 100%;
    padding: 40px 22px 0 22px;
    display: flex;
    align-items: center;
    justify-content: center;
  }
  .divider {
    width: 1px;
    height: 72%;
    background: var(--rule);
    flex: none;
  }
  .details {
    flex: 1;
    padding-left: 26px;
    padding-right: 12px;
    color: var(--ink);
  }

  .brand {
    display: flex;
    align-items: center;
    gap: 8px;
    white-space: nowrap;
  }
  .brand-mark {
    width: 16px; height: 16px;
    background: var(--orange);
    border-radius: 3px;
    flex: none;
  }
  .brand-name {
    color: var(--orange);
    font-weight: 400;
    font-size: 14px;
    line-height: 1.15;
  }
  .card-back .brand-mark { width: 24px; height: 24px; border-radius: 4px; }
  .card-back .brand-name { font-size: 22px; }

  .person-name { font-size: 21px; font-weight: 400; letter-spacing: 0.2px; }
  .person-title { font-size: 10px; color: var(--orange); margin-top: 2px; margin-bottom: 14px; }
  .contact-list { list-style: none; }
  .contact-list li {
    display: flex; align-items: center; gap: 8px;
    font-size: 12.5px; margin-bottom: 6px;
    white-space: nowrap;
  }
  .contact-icon {
    width: 13px; height: 13px;
    background: var(--orange);
    flex: none;
    display: flex; align-items: center; justify-content: center;
  }
  .address {
    font-style: normal;
    font-size: 12.5px;
    line-height: 1.3;
    margin-top: 20px;
    padding-left: 21px;
  }
</style>
</head>
<body>
  <section class="card card-front" aria-label="Business card front">
    <div class="front-panel">
      <div class="brand-area">
        <div class="brand">
          <span class="brand-mark"></span>
          <span class="brand-name">Brightwick Gadget Clinic</span>
        </div>
      </div>
      <div class="divider"></div>
      <div class="details">
        <h1 class="person-name">Marcus Delgrove</h1>
        <p class="person-title">Store Manager</p>
        <ul class="contact-list">
          <li>
            <span class="contact-icon">
              <svg width="9" height="9" viewBox="0 0 10 10"><path d="M2 1 L4 1 L4.6 3.2 L3.4 4 Q4.3 5.8 6 6.6 L6.8 5.4 L9 6 L9 8 Q8.5 9 7.5 9 Q1 8 1 2.5 Q1 1.5 2 1 Z" fill="#fff"/></svg>
            </span>
            (210) 555-0147
          </li>
          <li>
            <span class="contact-icon">
              <svg width="9" height="9" viewBox="0 0 10 10"><rect x="1" y="2.5" width="8" height="5.5" fill="none" stroke="#fff" stroke-width="1"/><path d="M1 2.5 L5 5.6 L9 2.5" fill="none" stroke="#fff" stroke-width="1"/></svg>
            </span>
            marcus@BrightwickClinic.com
          </li>
          <li>
            <span class="contact-icon">
              <svg width="9" height="9" viewBox="0 0 10 10"><circle cx="5" cy="5" r="3.8" fill="none" stroke="#fff" stroke-width="1"/><ellipse cx="5" cy="5" rx="1.6" ry="3.8" fill="none" stroke="#fff" stroke-width="0.8"/><line x1="1.2" y1="5" x2="8.8" y2="5" stroke="#fff" stroke-width="0.8"/></svg>
            </span>
            www.BrightwickClinic.com
          </li>
        </ul>
        <address class="address">
          4810 E Harlow Ridge Rd<br>
          Suite 417<br>
          San Antonio, TX 78163
        </address>
      </div>
    </div>
  </section>

  <section class="card card-back" aria-label="Business card back">
    <div class="brand">
      <span class="brand-mark"></span>
      <span class="brand-name">Brightwick Gadget Clinic</span>
    </div>
  </section>
</body>
</html>
```